I need a business card designed using the logo provided either vertical or horizontal......Harbourline Property Group is an Australian based real estate company that caters for the upper end of the market so the design of the business card "must reflect" the companies image!!
Colour combinations are optional but "must be realistic" and must be able to be accurately useable CMYK colours.
Please consider that any colours used "must be able to be used" and be suitable in following designs for "pull out banner signs" and "real estate signs".
The colours and the font in the attached designs are for example and other combinations are encouraged.
Target Market(s)
The High End of the Australian real estate market
Industry/Entity Type
Business
Contact Information for Business Card
Logo - Business Name - Director + Licensed Real Estate Agent - Mobile Number (Cell Phone) - Business Number - Fax - Email Address - Web address
Requirements
Must have
- Designs and colours (CMYK) that can easily be interpreted by an Australian printer.
Nice to have
- Some alternative ideas on colour and font..........the ones provided are ok and have been provided as an example but I am looking for alternative ideas
Should not have
- Loud, overly bright colours. Designs that do not reflect the professional standards of the business.
- Designs that look good on a computer monitor but can not be re-created on a printing press.............this is most important when it comes to shading etc.

```html
<!DOCTYPE html>
<html lang="en">
<head>
<meta charset="utf-8">
<title>Harbourline Property Group — Business Card</title>
<link href="https://fonts.googleapis.com/css2?family=Open+Sans:wght@400;600;700&display=swap" rel="stylesheet">
<style>
  :root {
    --backdrop: #e4e4e4;
    --card: #ffffff;
    --ink: #1e1e1e;
    --ink-soft: #3a3a3a;
    --gold: #c18a3a;
    --gold-light: #dcb46e;
    --sand: #dccb94;
    --shadow: rgba(0, 0, 0, 0.18);
  }
  * { margin: 0; padding: 0; box-sizing: border-box; }
  html, body {
    width: 1200px;
    height: 852px;
    overflow: hidden;
    background: var(--backdrop);
    font-family: "Open Sans", Arial, sans-serif;
    color: var(--ink);
  }
  .stage {
    width: 1200px;
    height: 852px;
    display: flex;
    align-items: center;
    justify-content: center;
    gap: 60px;
  }
  .card {
    position: relative;
    width: 500px;
    height: 286px;
    border-radius: 22px;
    background: var(--card);
    overflow: hidden;
    box-shadow: 0 6px 14px var(--shadow);
  }
  .brand {
    position: absolute;
    display: flex;
    align-items: center;
    gap: 10px;
    font-weight: 700;
    color: var(--ink);
    letter-spacing: 0.02em;
    white-space: nowrap;
  }
  .brand-mark {
    width: 14px;
    height: 14px;
    background: var(--gold);
    flex: none;
  }
  .card-front .brand {
    left: 0;
    right: 0;
    top: 128px;
    justify-content: center;
    font-size: 22px;
  }
  .card-back .brand {
    left: 30px;
    top: 110px;
    font-size: 16px;
  }
  .card-back .brand-mark {
    width: 12px;
    height: 12px;
  }
  .wave {
    position: absolute;
    inset: 0;
    width: 100%;
    height: 100%;
  }
  .holder {
    position: absolute;
    right: 24px;
    top: 12px;
    text-align: right;
  }
  .holder-name {
    font-size: 14px;
    line-height: 19px;
    font-weight: 700;
    color: var(--ink);
  }
  .holder-role {
    font-size: 10px;
    line-height: 14px;
    color: var(--ink-soft);
  }
  .contact {
    position: absolute;
    right: 22px;
    top: 104px;
    list-style: none;
    text-align: right;
    font-size: 10px;
    font-weight: 600;
    line-height: 16px;
    color: var(--ink);
  }
  .contact li {
    display: flex;
    justify-content: flex-end;
    align-items: center;
    gap: 8px;
    white-space: nowrap;
  }
  .contact svg {
    width: 10px;
    height: 10px;
    fill: var(--ink);
    flex: none;
  }
</style>
</head>
<body>
<main class="stage">

  <section class="card card-front" aria-label="Card front">
    <div class="brand"><span class="brand-mark"></span>Harbourline Property Group</div>
  </section>

  <section class="card card-back" aria-label="Card back">
    <svg class="wave" viewBox="0 0 500 286" preserveAspectRatio="none" aria-hidden="true">
      <defs>
        <linearGradient id="goldFill" x1="0" y1="1" x2="1" y2="0">
          <stop offset="0" stop-color="#b77d2e"/>
          <stop offset="0.55" stop-color="#d9ae66"/>
          <stop offset="1" stop-color="#c18a3a"/>
        </linearGradient>
      </defs>
      <path class="wave-line" d="M500,56 C394,58 322,102 281,152 C242,198 172,226 110,234" fill="none" stroke="var(--gold)" stroke-width="3.5"/>
      <path class="wave-sand" d="M500,64 C400,66 329,110 288,158 C249,208 168,234 0,243 L0,286 L500,286 Z" fill="var(--sand)"/>
      <path class="wave-gold" d="M500,72 C405,74 335,116 295,164 C255,214 172,240 0,250 L0,286 L500,286 Z" fill="url(#goldFill)"/>
      <path class="wave-gap" d="M500,72 C405,74 335,116 295,164 C255,214 172,240 0,250" fill="none" stroke="#ffffff" stroke-width="3"/>
    </svg>

    <div class="brand"><span class="brand-mark"></span>Harbourline Property Group</div>

    <div class="holder">
      <p class="holder-name">Your Long Name</p>
      <p class="holder-role">Managing Director</p>
    </div>

    <ul class="contact">
      <li>00.00.00.0000
        <svg viewBox="0 0 10 10"><path d="M2 1h2l1 2-1.2 1a5 5 0 0 0 2.2 2.2L7 5l2 1v2c0 .6-.4 1-1 1A8 8 0 0 1 1 2c0-.6.4-1 1-1z"/></svg></li>
      <li>00.00.00.0000
        <svg viewBox="0 0 10 10"><path d="M1 3h8v6H1zM3 1h4v2H3z"/></svg></li>
      <li>www.yourwebsite.com
        <svg viewBox="0 0 10 10"><circle cx="5" cy="5" r="4" fill="none" stroke="#1e1e1e" stroke-width="1.2"/><path d="M1 5h8M5 1v8" stroke="#1e1e1e" stroke-width="0.8"/></svg></li>
      <li>yourname@yourwebsite.com
        <svg viewBox="0 0 10 10"><path d="M1 2h8v6H1z"/><path d="M1 2l4 3.5L9 2" fill="none" stroke="#dcb46e" stroke-width="0.8"/></svg></li>
      <li>Your Commercial or office address
        <svg viewBox="0 0 10 10"><path d="M5 0.5a3.2 3.2 0 0 1 3.2 3.2C8.2 6 5 9.5 5 9.5S1.8 6 1.8 3.7A3.2 3.2 0 0 1 5 .5zm0 2a1.2 1.2 0 1 0 0 2.4 1.2 1.2 0 0 0 0-2.4z"/></svg></li>
    </ul>
  </section>

</main>
</body>
</html>
```